Redesign of business card for Cedar Ridge Mechanical

We are looking for a new design for our business cards for Cedar Ridge Mechanical. We are a plumbing & HVAC construction company, operating on the West Coast of Canada and USA. Logo attached.
Industry/Entity Type
Construction - Plumbing & HVAC
Contact Information for Business Card
Name, address, phone numbers, email, website address
Look and feel
Each slider illustrates characteristics of the customer's brand and the style your logo design should communicate.

```html
<!DOCTYPE html>
<html lang="en">
<head>
<meta charset="utf-8">
<title>Cedar Ridge Mechanical – Business Card</title>
<link href="https://fonts.googleapis.com/css2?family=Poppins:wght@300;400;600&display=swap" rel="stylesheet">
<style>
  :root {
    --backdrop: #d8d9da;
    --card: #e7e8e8;
    --ink: #151515;
    --ink-soft: #2a2a2a;
    --watermark: #d6d8d8;
    --emboss: #c8cbcb;
  }
  * { box-sizing: border-box; margin: 0; padding: 0; }
  html, body {
    width: 1200px; height: 780px; overflow: hidden;
    background: var(--backdrop);
    font-family: "Poppins", sans-serif;
    color: var(--ink);
  }
  .stage {
    width: 1200px; height: 780px;
    display: flex; align-items: center; justify-content: center; gap: 40px;
  }
  .card {
    position: relative;
    width: 530px; height: 303px;
    background: var(--card);
    overflow: hidden;
  }

  /* Front */
  .brand {
    position: absolute; top: 34px; right: 34px;
    display: flex; align-items: center; gap: 10px;
  }
  .brand-square { width: 22px; height: 22px; background: var(--ink); }
  .brand-name {
    font-weight: 600; font-size: 17px; letter-spacing: 0.02em;
    text-transform: uppercase; color: var(--ink);
  }
  .watermark {
    position: absolute; left: 26px; top: 120px;
    font-weight: 600; font-size: 40px; line-height: 1;
    text-transform: uppercase; color: var(--watermark);
    letter-spacing: 0.02em; white-space: nowrap;
  }
  .divider {
    position: absolute; left: 212px; right: 0; top: 138px;
    height: 1.5px; background: var(--ink);
  }
  .person { position: absolute; left: 30px; top: 104px; }
  .person-name { font-size: 30px; line-height: 1; white-space: nowrap; }
  .person-name .first { font-weight: 600; }
  .person-name .last { font-weight: 300; }
  .person-title { font-size: 14px; font-weight: 400; margin-top: 6px; color: var(--ink-soft); }

  .contact {
    position: absolute; right: 22px; top: 156px;
    text-align: right; font-size: 13.5px; font-weight: 400;
    line-height: 1.35; color: var(--ink-soft);
  }
  .contact .address { margin-bottom: 10px; padding-right: 24px; }
  .contact-line { display: flex; justify-content: flex-end; align-items: center; gap: 8px; }
  .contact-line svg { width: 14px; height: 14px; flex: none; }

  /* Back */
  .back { display: flex; align-items: center; justify-content: center; gap: 12px; }
  .back-square { width: 30px; height: 30px; background: var(--emboss); }
  .back-name {
    font-weight: 600; font-size: 26px; letter-spacing: 0.03em;
    text-transform: uppercase; color: var(--emboss);
  }
</style>
</head>
<body>
<main class="stage">
  <section class="card front" aria-label="Business card front">
    <div class="watermark" aria-hidden="true">Cedar Ridge</div>

    <div class="brand">
      <span class="brand-square"></span>
      <span class="brand-name">Cedar Ridge Mechanical</span>
    </div>

    <div class="divider"></div>

    <div class="person">
      <p class="person-name"><span class="first">Marta</span> <span class="last">Novakova</span></p>
      <p class="person-title">Founder &amp; CEO</p>
    </div>

    <address class="contact">
      <p class="address">1840 Harbor Ln. Suite 300<br>Bellingham, WA 98225</p>
      <p class="contact-line">(360) 555-0147
        <svg viewBox="0 0 16 16" aria-hidden="true"><path d="M4 1.5l2.2 2.6-1.3 1.6c.8 1.9 2.4 3.5 4.3 4.3l1.6-1.3 2.6 2.2-1.5 2.3C7.4 13.2 2.8 8.6 1.7 3z" fill="#151515"/></svg>
      </p>
      <p class="contact-line">info@cedarridgemech.com
        <svg viewBox="0 0 16 16" aria-hidden="true"><rect x="1.5" y="3.5" width="13" height="9" fill="none" stroke="#151515" stroke-width="1.4"/><path d="M1.5 3.5L8 9l6.5-5.5" fill="none" stroke="#151515" stroke-width="1.4"/></svg>
      </p>
      <p class="contact-line">www.cedarridgemech.com
        <svg viewBox="0 0 16 16" aria-hidden="true"><circle cx="8" cy="8" r="6.3" fill="none" stroke="#151515" stroke-width="1.4"/><ellipse cx="8" cy="8" rx="2.6" ry="6.3" fill="none" stroke="#151515" stroke-width="1.1"/><path d="M1.7 8h12.6" stroke="#151515" stroke-width="1.1"/></svg>
      </p>
    </address>
  </section>

  <section class="card back" aria-label="Business card back">
    <span class="back-square"></span>
    <span class="back-name">Cedar Ridge Mechanical</span>
  </section>
</main>
</body>
</html>
```